dsadasdasdasdsa

Industry/Entity Type

Mortgage Broking

Requirements
Must have
• Call-to-action button somewhere on the graphic
Nice to have
• The font of our logo is Montserrat

```html
<!DOCTYPE html>
<html lang="en">
<head>
<meta charset="UTF-8">
<title>Mortgage Broker Directory Banner</title>
<link href="https://fonts.googleapis.com/css2?family=Montserrat:wght@600;800;900&display=swap" rel="stylesheet">
<style>
  :root {
    --page-bg: #ffffff;
    --red-start: #c23b2a;
    --red-end: #9e2c1f;
    --green-start: #0d4a2a;
    --green-mid: #146b3c;
    --green-end: #1f9a5e;
    --cta-yellow: #f2f23a;
    --headline-yellow: #e4f23a;
    --mint: #3ef0a2;
    --white: #ffffff;
    --mascot-skin: #5cae4a;
    --mascot-shell: #7a5a36;
  }
  * { margin: 0; padding: 0; box-sizing: border-box; }
  html, body {
    width: 1200px;
    height: 180px;
    overflow: hidden;
    background: var(--page-bg);
  }
  .banner {
    position: relative;
    width: 1200px;
    height: 180px;
    font-family: "Montserrat", sans-serif;
  }
  .banner-band {
    position: absolute;
    left: 40px;
    top: 29px;
    width: 1135px;
    height: 126px;
    border-radius: 14px;
    overflow: hidden;
    display: flex;
  }
  .band-red {
    width: 460px;
    height: 100%;
    background: linear-gradient(90deg, var(--red-start), var(--red-end));
  }
  .band-green {
    flex: 1;
    height: 100%;
    background: linear-gradient(100deg, var(--green-start) 0%, var(--green-mid) 45%, var(--green-end) 100%);
  }
  .mascot {
    position: absolute;
    left: 215px;
    top: 0;
    width: 230px;
    height: 100%;
    background: linear-gradient(180deg, var(--mascot-skin) 0%, #3f8a3a 55%, var(--mascot-shell) 100%);
    opacity: 0.85;
  }
  .cta-button {
    position: absolute;
    left: 61px;
    top: 73px;
    width: 177px;
    height: 40px;
    border: 2px solid var(--white);
    border-radius: 20px;
    display: flex;
    align-items: center;
    justify-content: center;
    color: var(--cta-yellow);
    font-weight: 800;
    font-size: 19px;
    text-decoration: none;
  }
  .message {
    position: absolute;
    left: 498px;
    top: 34px;
  }
  .message-question {
    color: var(--headline-yellow);
    font-weight: 600;
    font-size: 32px;
    line-height: 36px;
    white-space: nowrap;
  }
  .message-action {
    color: var(--mint);
    font-weight: 900;
    font-size: 35px;
    line-height: 31px;
    text-transform: uppercase;
    margin-top: 4px;
    white-space: nowrap;
  }
</style>
</head>
<body>
  <div class="banner">
    <div class="banner-band">
      <div class="band-red"></div>
      <div class="band-green"></div>
      <div class="mascot" role="img" aria-label="Cartoon turtle mascot holding a small house"></div>
    </div>
    <a class="cta-button" href="#">CLICK HERE</a>
    <div class="message">
      <p class="message-question">Need a Mortgage Broker?</p>
      <p class="message-action">Search now on Australia’s<br>largest directory</p>
    </div>
  </div>
</body>
</html>
```